Brightmill Data Works

Our company is about IT hardwares and IT solutions. IT hardware such as PC, RAMS, storage and servers. IT solutions such as project management, BA. We are also selling new technology too.

Target Market(s)

Consumer, Small to Medium Business, Corporate

Requirements
Must have
• The business card must have the following:
• Name:
• Title:
• Contact Number:
• Email address:
• Website:
• Color: Must match the logo color upgrade

```html
<!DOCTYPE html>
<html lang="en">
<head>
<meta charset="utf-8">
<title>Brightmill Data Works – Business Card</title>
<link rel="stylesheet" href="https://fonts.googleapis.com/css2?family=Roboto:wght@300;400;500;700&display=swap">
<style>
  :root {
    --backdrop: #3a322d;
    --card: #1d2023;
    --card-edge: #15171a;
    --copper: #c98a3e;
    --amber: #f0a233;
    --steel: #5c6064;
    --ink-light: #f2f2f2;
    --rule: #9a9ea2;
    --muted: #8e9296;
  }
  * { margin: 0; padding: 0; box-sizing: border-box; }
  html, body { width: 1200px; height: 769px; overflow: hidden; }
  body {
    background: var(--backdrop);
    font-family: "Roboto", Arial, sans-serif;
    position: relative;
  }
  .card {
    position: absolute;
    width: 520px;
    height: 297px;
    background: var(--card);
    border-radius: 3px;
    box-shadow: 0 10px 28px rgba(0,0,0,.45), 0 0 0 1px var(--card-edge);
  }
  .card--front { left: 70px; top: 70px; }
  .card--back { left: 610px; top: 400px; }

  /* Front */
  .front-name {
    position: absolute;
    left: 0; right: 0; top: 112px;
    text-align: center;
    color: var(--copper);
    font-weight: 700;
    font-size: 26px;
    letter-spacing: 1px;
  }
  .front-web {
    position: absolute;
    left: 0; right: 0; top: 200px;
    text-align: center;
    color: var(--muted);
    font-weight: 300;
    font-size: 13px;
    letter-spacing: 4px;
  }

  /* Back */
  .brand {
    position: absolute;
    right: 40px; top: 52px;
    display: flex;
    align-items: center;
    gap: 10px;
  }
  .brand-square { width: 14px; height: 14px; background: var(--amber); }
  .brand-name {
    color: var(--steel);
    font-weight: 700;
    font-size: 20px;
    letter-spacing: .5px;
  }
  .person { position: absolute; left: 34px; top: 90px; }
  .person-name {
    color: var(--amber);
    font-weight: 500;
    font-size: 19px;
  }
  .person-title {
    color: var(--ink-light);
    font-size: 14px;
    margin-top: 2px;
  }
  .rule {
    position: absolute;
    left: 34px; right: 40px; top: 145px;
    height: 1px;
    background: var(--rule);
  }
  .contacts { position: absolute; left: 34px; top: 158px; list-style: none; }
  .contacts li {
    display: flex; align-items: center; gap: 8px;
    color: var(--ink-light);
    font-size: 13px;
    margin-bottom: 7px;
  }
  .contacts svg { width: 11px; height: 11px; fill: var(--amber); }
  .back-web {
    position: absolute;
    right: 40px; bottom: 30px;
    color: var(--ink-light);
    font-size: 15px;
  }
</style>
</head>
<body>
  <section class="card card--front">
    <div class="front-name">Brightmill Data Works</div>
    <div class="front-web">www.brightmilldata.com</div>
  </section>

  <section class="card card--back">
    <div class="brand">
      <span class="brand-square"></span>
      <span class="brand-name">Brightmill Data Works</span>
    </div>
    <div class="person">
      <div class="person-name">DANIEL MARSH</div>
      <div class="person-title">CEO/FOUNDER</div>
    </div>
    <div class="rule"></div>
    <ul class="contacts">
      <li>
        <svg viewBox="0 0 24 24" aria-hidden="true"><path d="M6.6 10.8a15.1 15.1 0 0 0 6.6 6.6l2.2-2.2a1 1 0 0 1 1-.25 11.4 11.4 0 0 0 3.6.57 1 1 0 0 1 1 1V20a1 1 0 0 1-1 1A17 17 0 0 1 3 4a1 1 0 0 1 1-1h3.5a1 1 0 0 1 1 1c0 1.25.2 2.45.57 3.57a1 1 0 0 1-.25 1z"/></svg>
        555 210 4873
      </li>
      <li>
        <svg viewBox="0 0 24 24" aria-hidden="true"><path d="M2 5h20v14H2z M2 5l10 8 10-8" /></svg>
        daniel@brightmilldata.com
      </li>
    </ul>
    <div class="back-web">www.brightmilldata.com</div>
  </section>
</body>
</html>
```